Money Mindset Podcast needs fun, creative cover art

Launching a new podcast called 'Turning Your Thoughts Toward Savings' - aimed at an audience 30-50 who are interested in the practicalities of managing their money but also the more mental and emotional aspects.
Looking for something not too serious, warm and friendly.

Must be easy to read on phone screens
3000 x 3000 in size
Avoid currency symbols $, £ etc, as may have an international audience

Target Market(s)

Podcast listeners age 30-50 starting in the UK but then worldwide. Probably 60:40 female bias

Industry/Entity Type

Life Coaching

Font styles to use
Serif
Sans Serif

Colors
cadf82
fee18a
acd037
85cae6
eea4c8
f59195
85acd3

Requirements
Must have
• Simple, clear design. Easy to read on variety of devices. 3000 x 3000
Appeal to those with a spiritual or emotional interests
Nice to have
• Stand out among other money related podcasts
Maybe play around with clouds, lightbulbs and clearing skies
Should not have
• Currency symbols such as $ or £
Be too corporate or bank like
Stock images

```html
<!DOCTYPE html>
<html lang="en">
<head>
<meta charset="utf-8">
<title>Turning Your Thoughts Toward Savings</title>
<link href="https://fonts.googleapis.com/css2?family=Andika:wght@400;700&display=swap" rel="stylesheet">
<style>
  :root {
    --night: #1a1f4b;
    --night-glow: #2a3166;
    --mist: #d9e4e1;
    --sun: #fee100;
    --title-font: "Andika", "Trebuchet MS", sans-serif;
  }
  html, body {
    margin: 0;
    padding: 0;
    width: 1200px;
    height: 1200px;
    overflow: hidden;
    background: var(--night);
  }
  .cover {
    position: relative;
    width: 1200px;
    height: 1200px;
    background: var(--night);
    overflow: hidden;
    font-family: var(--title-font);
  }
  .sky-backdrop {
    position: absolute;
    inset: 0;
    background: radial-gradient(circle at 51% 47%, var(--night-glow) 0%, var(--night) 70%);
  }
  .podcast-title {
    margin: 0;
    font-weight: 400;
  }
  .title-line {
    position: absolute;
    margin: 0;
    line-height: 1;
    white-space: nowrap;
    font-weight: 400;
  }
  .title-lead {
    left: 245px;
    top: 330px;
    font-size: 100px;
    color: var(--mist);
    transform: rotate(-10deg);
    transform-origin: left bottom;
  }
  .title-key {
    left: 215px;
    top: 433px;
    font-size: 190px;
    color: var(--sun);
    letter-spacing: -1px;
  }
  .title-link {
    left: 1000px;
    top: 268px;
    font-size: 72px;
    color: var(--sun);
    writing-mode: vertical-rl;
    transform: rotate(180deg);
  }
  .title-end {
    left: 170px;
    top: 615px;
    font-size: 260px;
    color: var(--mist);
    letter-spacing: -2px;
    transform: rotate(-4deg);
    transform-origin: left bottom;
  }
</style>
</head>
<body>
<main class="cover">
  <div class="sky-backdrop" role="img" aria-label="Radiating sunburst of light dots spreading out from the centre across a night-blue sky"></div>

  <h1 class="podcast-title" aria-label="Turning Your Thoughts Toward Savings">
    <span class="title-line title-lead">turning your</span>
    <span class="title-line title-key">thoughts</span>
    <span class="title-line title-link">toward</span>
    <span class="title-line title-end">savings</span>
  </h1>
</main>
</body>
</html>
```